Young, dynamic furniture company needs a new business card design

We require a new business card design for our modern furniture company which supplies furniture and appliances to the property and development market.
Oakridge Interiors has become one of the leading furniture & appliance suppliers to the property market withing London. With over 10 years experience, we have increased our business to supply not only private landlords and managing agents, but also property developers, housing associations and local councils.
We offer not only a complete range of furniture which includes beds, wardrobes, dining sets and sofas, but also a high quality, full delivery and assembly service to help you with all our furnishing needs.

Target Market(s)

Private landlords, estate agents, letting agents, property management companies

Industry/Entity Type

Business

Contact Information for Business Card

Name,
Title,
Address,
Mobile,
Telephone,
Fax, Website, email address

Font styles to use
Sans Serif

Colors
3176b5
0555a3
85abd2
cfdeed

Requirements
Must have
• All the above information for each of our staff, along with our logo

```html
<!DOCTYPE html>
<html lang="en">
<head>
<meta charset="utf-8">
<title>Oakridge Interiors – Business Card</title>
<link href="https://fonts.googleapis.com/css2?family=Open+Sans:wght@400;600;700&display=swap" rel="stylesheet">
<style>
  :root {
    --page-bg: #e6e7ea;
    --card-face: #f3f4f6;
    --card-edge: #d3d6dc;
    --panel-dark: #0c1638;
    --panel-mid: #1a2b66;
    --accent-blue: #3176b5;
    --accent-deep: #0555a3;
    --ink-dark: #23262d;
    --ink-light: #e6eaf3;
    --ink-soft: #c7d0e2;
  }
  * { margin: 0; padding: 0; box-sizing: border-box; }
  html, body {
    width: 1200px; height: 969px; overflow: hidden;
    background: var(--page-bg);
    font-family: "Open Sans", Arial, sans-serif;
  }
  .business-card {
    position: absolute;
    left: 100px; top: 200px;
    width: 1000px; height: 568px;
    background: var(--card-face);
    border: 1px solid var(--card-edge);
    overflow: hidden;
    box-shadow: 0 10px 30px rgba(20, 30, 60, 0.18);
  }
  .accent-stripe {
    position: absolute; inset: 0;
    background: linear-gradient(180deg, var(--accent-blue), var(--accent-deep));
    clip-path: polygon(75.6% 0, 76.9% 0, 28.9% 100%, 27.6% 100%);
  }
  .info-panel {
    position: absolute; inset: 0;
    background: linear-gradient(120deg, var(--panel-mid) 0%, var(--panel-dark) 70%);
    clip-path: polygon(78% 0, 100% 0, 100% 100%, 30.2% 100%);
  }
  .brand {
    position: absolute;
    left: 90px; top: 238px;
    width: 400px;
  }
  .brand-name {
    display: flex; align-items: center; gap: 14px;
    font-size: 33px; font-weight: 600;
    color: var(--ink-dark);
    letter-spacing: 0.5px;
    text-transform: uppercase;
    white-space: nowrap;
  }
  .brand-square {
    width: 26px; height: 26px;
    background: var(--accent-deep);
    flex: none;
  }
  .brand-tagline {
    margin-top: 6px;
    margin-left: 40px;
    font-size: 15px; font-weight: 700;
    color: var(--ink-dark);
    letter-spacing: 0.6px;
    text-transform: uppercase;
  }
  .contact {
    position: absolute;
    right: 36px; top: 108px;
    text-align: right;
    color: var(--ink-light);
  }
  .person-name {
    font-size: 30px; font-weight: 400; letter-spacing: 1.5px;
    text-transform: uppercase;
  }
  .person-title {
    font-size: 24px; letter-spacing: 1px; color: var(--ink-soft);
    text-transform: uppercase;
    margin-top: 2px;
  }
  .address {
    margin-top: 90px;
    font-size: 24px; line-height: 37px;
    color: var(--ink-soft);
  }
  .contact-list {
    list-style: none;
    margin-top: 14px;
    font-size: 23px; line-height: 38px;
    color: var(--ink-soft);
  }
  .contact-list li {
    display: flex; justify-content: flex-end; align-items: center; gap: 10px;
  }
  .contact-icon { width: 22px; height: 22px; flex: none; }
</style>
</head>
<body>
  <div class="business-card">
    <div class="accent-stripe"></div>
    <div class="info-panel"></div>

    <div class="brand">
      <div class="brand-name"><span class="brand-square"></span>Oakridge Interiors</div>
      <div class="brand-tagline">Trade Furniture Solutions</div>
    </div>

    <div class="contact">
      <div class="person-name">Daniel Mercer</div>
      <div class="person-title">President</div>
      <div class="address">2217 Harlow Lane<br>Maple Grove, NY 11420</div>
      <ul class="contact-list">
        <li>555 0148 2291
          <svg class="contact-icon" viewBox="0 0 24 24" aria-hidden="true"><path fill="#c7d0e2" d="M6.6 10.8a15 15 0 0 0 6.6 6.6l2.2-2.2a1 1 0 0 1 1-.25 11.4 11.4 0 0 0 3.6.57 1 1 0 0 1 1 1V20a1 1 0 0 1-1 1A17 17 0 0 1 3 4a1 1 0 0 1 1-1h3.5a1 1 0 0 1 1 1c0 1.25.2 2.45.57 3.57a1 1 0 0 1-.25 1z"/></svg>
        </li>
        <li>555 0173 6604
          <svg class="contact-icon" viewBox="0 0 24 24" aria-hidden="true"><rect x="6" y="2" width="12" height="20" rx="2" fill="none" stroke="#c7d0e2" stroke-width="2"/><circle cx="12" cy="18" r="1.2" fill="#c7d0e2"/></svg>
        </li>
        <li>555 0192 3318
          <svg class="contact-icon" viewBox="0 0 24 24" aria-hidden="true"><rect x="7" y="3" width="10" height="6" fill="none" stroke="#c7d0e2" stroke-width="2"/><rect x="3" y="9" width="18" height="9" rx="1.5" fill="#c7d0e2"/><rect x="7" y="15" width="10" height="6" fill="#c7d0e2" stroke="#0c1638" stroke-width="1.5"/></svg>
        </li>
        <li>daniel@oakridge.com
          <svg class="contact-icon" viewBox="0 0 24 24" aria-hidden="true"><rect x="3" y="6" width="18" height="13" fill="#c7d0e2"/><path d="M3 6l9 7 9-7" fill="none" stroke="#0c1638" stroke-width="1.5"/></svg>
        </li>
        <li>www.oakridge.com
          <svg class="contact-icon" viewBox="0 0 24 24" aria-hidden="true"><circle cx="12" cy="12" r="9" fill="#c7d0e2"/><path d="M3 12h18M12 3c3 3 3 15 0 18M12 3c-3 3-3 15 0 18" fill="none" stroke="#0c1638" stroke-width="1.3"/></svg>
        </li>
      </ul>
    </div>
  </div>
</body>
</html>
```